Communication and Marketing agency needs a new presentation card

We are a group of communication and marketing agencies specialized in companies that are in the logistics and industrial sector. The head agency is TELVANO Grupo and the group consists of 4 agencies: TELVANO Media, TELVANO Digital, TELVANO Research and DifundeEnPantalla. We hace 4 offices in Spain (Madrid, Barcelona, Valencia and Murcia). We are looking for a clean and attractive design that transmits our experience, brand presence in the market and knowledge to those who receive the card.It has to maintain the colors of the logo that is attached.
Target Market(s)
logistics and industrial sector
Marketing department
Contact Information for Business Card
Clean and attractive design

```html
<!DOCTYPE html>
<html lang="es">
<head>
<meta charset="utf-8">
<title>TELVANO Grupo – Tarjeta de visita</title>
<link rel="stylesheet" href="https://fonts.googleapis.com/css2?family=Roboto:wght@400;500;700&family=Montserrat:wght@400&display=swap">
<style>
  :root {
    --brand-red: #ad2427;
    --band-grey: #54504d;
    --paper: #ffffff;
    --backdrop: #e3e3e3;
    --ink-light: #ffffff;
  }
  * { box-sizing: border-box; margin: 0; padding: 0; }
  html, body {
    width: 1125px;
    height: 1200px;
    overflow: hidden;
    background: var(--backdrop);
    font-family: "Roboto", Arial, sans-serif;
  }
  .card {
    position: absolute;
    left: 171px;
    width: 826px;
    height: 472px;
    overflow: hidden;
  }
  .card--front { top: 106px; background: var(--brand-red); }
  .card--back { top: 639px; background: var(--brand-red); }

  /* Front */
  .front-brand-panel {
    position: absolute;
    left: 0; top: 0;
    width: 419px; height: 100%;
    background: var(--paper);
  }
  .front-brand-name {
    position: absolute;
    left: 0; top: 188px;
    width: 419px;
    text-align: center;
    color: var(--brand-red);
    font-weight: 500;
    font-size: 44px;
    line-height: 1.05;
    letter-spacing: 1px;
  }
  .contact-block {
    position: absolute;
    left: 474px; top: 132px;
    color: var(--ink-light);
  }
  .contact-name { font-weight: 700; font-size: 29px; line-height: 1.1; }
  .contact-role { font-weight: 500; font-size: 20px; margin-top: 1px; }
  .contact-list { list-style: none; margin-top: 18px; }
  .contact-list li {
    display: flex;
    align-items: center;
    gap: 11px;
    font-size: 19.5px;
    line-height: 26px;
  }
  .contact-list svg { width: 18px; height: 18px; flex: none; fill: var(--ink-light); }
  .office-band {
    position: absolute;
    left: 0; top: 394px;
    width: 100%; height: 38px;
    background: var(--band-grey);
    color: var(--ink-light);
    font-family: "Montserrat", Arial, sans-serif;
    font-size: 19px;
    letter-spacing: 0.5px;
    display: flex;
    justify-content: center;
    align-items: center;
    gap: 14px;
  }
  .office-band .divider { opacity: 0.9; }

  /* Back */
  .group-name {
    position: absolute;
    left: 0; top: 158px;
    width: 100%;
    text-align: center;
    color: var(--ink-light);
    font-weight: 500;
    font-size: 70px;
    line-height: 1.05;
    letter-spacing: 2px;
  }
  .agency-row {
    position: absolute;
    left: 0; top: 385px;
    width: 100%;
    display: flex;
    justify-content: center;
    gap: 38px;
  }
  .agency-name {
    width: 134px;
    color: var(--ink-light);
    font-weight: 500;
    font-size: 18px;
    line-height: 1.1;
    text-align: center;
  }
</style>
</head>
<body>

<section class="card card--front" aria-label="Tarjeta, anverso">
  <div class="front-brand-panel">
    <p class="front-brand-name">TELVANO<br>Media</p>
  </div>

  <div class="contact-block">
    <p class="contact-name">Lorenzo Badía</p>
    <p class="contact-role">Director</p>
    <ul class="contact-list">
      <li>
        <svg viewBox="0 0 24 24" aria-hidden="true"><path d="M6.6 10.8a15 15 0 0 0 6.6 6.6l2.2-2.2c.3-.3.7-.4 1-.2 1.1.4 2.3.6 3.6.6.6 0 1 .4 1 1V20c0 .6-.4 1-1 1A17 17 0 0 1 3 4c0-.6.4-1 1-1h3.5c.6 0 1 .4 1 1 0 1.3.2 2.5.6 3.6.1.3 0 .7-.2 1z"/></svg>
        913 472 658
      </li>
      <li>
        <svg viewBox="0 0 24 24" aria-hidden="true"><path d="M7 1h10a2 2 0 0 1 2 2v18a2 2 0 0 1-2 2H7a2 2 0 0 1-2-2V3a2 2 0 0 1 2-2zm0 3v14h10V4zm5 15.5a1 1 0 1 0 0 2 1 1 0 0 0 0-2z"/></svg>
        645 218 730
      </li>
      <li>
        <svg viewBox="0 0 24 24" aria-hidden="true"><path d="M2 5h20v14H2zm2 2v.5l8 5 8-5V7zm0 2.8V17h16V9.8l-8 5z"/></svg>
        lbadia@telvano.es
      </li>
      <li>
        <svg viewBox="0 0 24 24" aria-hidden="true"><rect x="3" y="3" width="18" height="18" rx="2"/></svg>
        lorenzobadia
      </li>
      <li>
        <svg viewBox="0 0 24 24" aria-hidden="true"><path d="M12 2a10 10 0 1 0 0 20 10 10 0 0 0 0-20zm-1 17.9A8 8 0 0 1 4.2 10L9 14.8V16a2 2 0 0 0 2 2zm6.9-2.5A2 2 0 0 0 16 16h-1v-3a1 1 0 0 0-1-1H8v-2h2a1 1 0 0 0 1-1V7h2a2 2 0 0 0 2-2v-.4a8 8 0 0 1 2.9 12.8z"/></svg>
        telvano.es
      </li>
    </ul>
  </div>

  <div class="office-band">
    <span>MADRID</span><span class="divider">|</span>
    <span>BARCELONA</span><span class="divider">|</span>
    <span>VALENCIA</span><span class="divider">|</span>
    <span>MURCIA</span>
  </div>
</section>

<section class="card card--back" aria-label="Tarjeta, reverso">
  <p class="group-name">TELVANO<br>Grupo</p>
  <div class="agency-row">
    <p class="agency-name">TELVANO<br>Digital</p>
    <p class="agency-name">TELVANO<br>Media</p>
    <p class="agency-name">TELVANO<br>Research</p>
    <p class="agency-name">Difunde<br>EnPantalla</p>
  </div>
</section>

</body>
</html>
```